Design material for Lumora Event

We need a design of POSM for Lumora Event
1. Content:
- The Lumora Event 3rd
- Singapore 28.10.2018
- A placeholder for insert logo of sponsors (limit 10 logo)
2. POSM:
- Backdrop: 5,5m and 2,6m
- Banner: 4m and 0,5m
- Standee: 0,8m and 2m
- Cover: A4 size
3. Style:
We need style simply because we are a hospital.
Main color: light blue and a little of green (if can)

Hope to see your design soon!

Font styles to use
Sans Serif

Colors
0792cd
85cae6
86cfc6
33b8a4
33a6d7

```html
<!DOCTYPE html>
<html lang="en">
<head>
<meta charset="utf-8">
<title>Lumora Event – Standee</title>
<link rel="stylesheet" href="https://fonts.googleapis.com/css2?family=Montserrat:wght@400;600;700&family=Quicksand:wght@700&display=swap">
<style>
  :root {
    --page-bg: #f3f4f5;
    --banner-bg: #ffffff;
    --navy: #1d5a86;
    --blue: #0792cd;
    --sky: #85cae6;
    --mint: #86cfc6;
    --teal: #33b8a4;
    --line-blue: #33a6d7;
    --ink: #2b2b2b;
  }
  html, body {
    margin: 0;
    padding: 0;
    width: 1200px;
    height: 906px;
    overflow: hidden;
    background: var(--page-bg);
  }
  .standee {
    position: absolute;
    left: 398px;
    top: 18px;
    width: 404px;
    height: 870px;
    box-shadow: 0 2px 10px rgba(0,0,0,0.12);
  }
  .standee svg { display: block; width: 100%; height: 100%; }
  .title { font-family: "Quicksand", sans-serif; font-weight: 700; fill: var(--navy); }
  .edition { font-family: "Montserrat", sans-serif; font-weight: 700; fill: #fff; }
  .site { font-family: "Quicksand", sans-serif; font-weight: 700; fill: var(--mint); }
  .city { font-family: "Montserrat", sans-serif; font-weight: 600; fill: var(--teal); letter-spacing: 3px; }
  .weekday { font-family: "Montserrat", sans-serif; font-weight: 700; fill: var(--teal); }
  .day { font-family: "Montserrat", sans-serif; font-weight: 700; fill: var(--blue); }
  .month { font-family: "Montserrat", sans-serif; font-weight: 400; fill: var(--blue); }
  .year { font-family: "Montserrat", sans-serif; font-weight: 700; fill: #fff; }
  .sponsor { font-family: "Montserrat", sans-serif; font-weight: 700; fill: var(--ink); font-size: 6.5px; }
</style>
</head>
<body>
  <div class="standee">
    <svg viewBox="0 0 302 650" xmlns="http://www.w3.org/2000/svg">
      <defs>
        <linearGradient id="lattice-tone" x1="0" y1="0" x2="0" y2="1">
          <stop offset="0" stop-color="#e6e9ec"/>
          <stop offset="1" stop-color="#ffffff"/>
        </linearGradient>
        <linearGradient id="skyline-tone" x1="0" y1="0" x2="0" y2="1">
          <stop offset="0" stop-color="#7fa7c9"/>
          <stop offset="0.55" stop-color="#d9d3c0"/>
          <stop offset="0.75" stop-color="#8c8a85"/>
          <stop offset="1" stop-color="#4e5a63"/>
        </linearGradient>
        <clipPath id="banner-clip"><rect width="302" height="650"/></clipPath>
      </defs>

      <g clip-path="url(#banner-clip)">
        <rect class="banner-bg" width="302" height="650" fill="var(--banner-bg)"/>
        <rect class="backdrop-photo" width="302" height="340" fill="url(#lattice-tone)" role="img" aria-label="Faint white architectural lattice in the background"/>

        <!-- edition flag -->
        <polygon class="edition-flag" points="0,3 22,3 90,78 0,153" fill="var(--teal)"/>
        <text class="edition" x="16" y="93" font-size="30">3<tspan font-size="10" dy="-15">rd</tspan></text>

        <!-- title -->
        <text class="title" x="98" y="63" font-size="36">Lumora</text>
        <text class="title" x="98" y="106" font-size="36">Event</text>
        <text class="site" x="100" y="140" font-size="11">LumoraEvent.com</text>

        <!-- date block -->
        <text class="city" x="297" y="185" font-size="10" text-anchor="end">SINGAPORE</text>
        <text class="weekday" x="297" y="215" font-size="27" text-anchor="end">SUNDAY</text>
        <text class="day" x="297" y="256" font-size="48" text-anchor="end">28</text>
        <text class="month" x="297" y="277" font-size="17" text-anchor="end">OCTOBER</text>

        <!-- thin guide lines -->
        <line x1="150" y1="200" x2="296" y2="346" stroke="var(--line-blue)" stroke-width="0.6"/>
        <line x1="100" y1="520" x2="296" y2="470" stroke="var(--line-blue)" stroke-width="0.6"/>
        <line x1="210" y1="510" x2="294" y2="440" stroke="var(--line-blue)" stroke-width="0.6"/>

        <!-- diamond cluster -->
        <polygon class="diamond-mint" points="109,175 207,273 109,371 11,273" fill="var(--mint)"/>
        <polygon class="diamond-navy" points="30,300 120,390 30,480 -60,390" fill="var(--navy)"/>
        <polygon class="diamond-sky" points="112,336 202,426 112,516 22,426" fill="var(--sky)"/>
        <polygon class="diamond-frame" points="107,214 231,338 107,462 -17,338" fill="#ffffff"/>
        <polygon class="skyline-photo" points="107,224 221,338 107,452 -7,338" fill="url(#skyline-tone)" role="img" aria-label="Photo of the Singapore waterfront skyline at sunset"/>
        <polygon class="diamond-year" points="230,313 290,373 230,433 170,373" fill="var(--teal)"/>
        <text class="year" x="230" y="380" font-size="19" text-anchor="middle">2018</text>

        <!-- sponsors, row one -->
        <g class="sponsor-row">
          <text class="sponsor" x="30" y="572" text-anchor="middle">Bluecrest</text>
          <text class="sponsor" x="84" y="572" text-anchor="middle">Cedarline</text>
          <text class="sponsor" x="136" y="572" text-anchor="middle">Greenfold</text>
          <text class="sponsor" x="182" y="572" text-anchor="middle">Norvia</text>
          <text class="sponsor" x="228" y="572" text-anchor="middle">Kestrel</text>
          <text class="sponsor" x="276" y="568" text-anchor="middle">Harbor Row</text>
          <text class="sponsor" x="276" y="576" text-anchor="middle">Club</text>
        </g>
        <!-- sponsors, row two -->
        <g class="sponsor-row">
          <text class="sponsor" x="36" y="626" text-anchor="middle">Harbor Row</text>
          <text class="sponsor" x="36" y="634" text-anchor="middle">Club</text>
          <text class="sponsor" x="96" y="630" text-anchor="middle">Trailnest</text>
          <text class="sponsor" x="152" y="630" text-anchor="middle">Ridgeway</text>
          <text class="sponsor" x="208" y="630" text-anchor="middle">Westbay Kayak</text>
          <rect x="255" y="623" width="7" height="7" fill="var(--ink)"/>
          <text class="sponsor" x="265" y="630">Halden</text>
        </g>
      </g>
    </svg>
  </div>
</body>
</html>
```